http://www.brindlewares.com/ New Ecommerce Site

We are redesigning Brindlewares.com on shopvantly.com.

We need to get a design for the ecommerce site.

They have about 15-45 products and these are the menu items that they need on the pages.

Knives:
Kitchen Knives
Neck Knives
Outdoor Knives
Bluefinch Knives
Clearance Knives
Premium Knives
Misc. Product:
Waterstones
Books
DVDs
T-Shirts
Scissors
Bladesmithing School
Videos
Links
Testimonials/Feedback
Contact Dennis Form
Knife Care and Maintenance Tips
Knife Sharpening
Knife Archives
Kitchen Knife Archives

We need several pages designed.

- Category Page
- Single Item page
- Knive Archive Pages (This is where old knives are stored that are not being sold anymore)
- Featured Product pages.
- Information pages
- checkout

The design has to be VERY elagant, like vostel.com.
And it has to be very easy to navigate and buy items like http://bladesgoquick.com/

Thanks,
Peter Hollis

Requirements
Must have
• Must be very elegant, and have the menu items somewhere on the pages.

```html
<!DOCTYPE html>
<html lang="en">
<head>
<meta charset="utf-8">
<title>Brindlewares – Kitchen Knives</title>
<link href="https://fonts.googleapis.com/css2?family=Source+Sans+3:wght@400;600&family=Oswald:wght@500&display=swap" rel="stylesheet">
<style>
:root{
  --ink:#2b2b2b;
  --muted:#555;
  --red:#a50f0f;
  --red-text:#b5120f;
  --dark:#1d1d1d;
  --band:#efefef;
  --line:#e2e2e2;
  --footer:#ececec;
  --white:#fff;
}
*{box-sizing:border-box;margin:0;padding:0}
html,body{width:860px;height:1200px;overflow:hidden}
body{font-family:"Source Sans 3",Arial,sans-serif;color:var(--ink);background:var(--white);position:relative}
a{color:inherit;text-decoration:none}

.top-bar{height:36px;background:var(--dark);color:var(--white);display:flex;align-items:center;justify-content:space-between;padding:0 63px 0 83px;font-size:10px;font-weight:600}
.top-links{display:flex;gap:10px}
.top-links span.sep{opacity:.8}
.cart{font-size:11px;font-weight:400;display:flex;align-items:center;gap:6px}

.site-header{height:80px;position:relative;border-bottom:1px solid var(--line)}
.brand{position:absolute;left:62px;top:10px}
.brand-name{font-size:27px;font-weight:400;color:#8c8c8c;letter-spacing:1px;line-height:1;text-transform:uppercase}
.brand-tag{font-size:8.5px;color:var(--muted);margin-top:16px}
.search{position:absolute;left:635px;top:27px;width:162px;height:24px;border:1px solid #cfcfcf;border-radius:2px;font-size:9px;color:#999;font-style:italic;padding:5px 4px;display:flex;justify-content:space-between}

.main-nav{height:43px;background:var(--band);display:flex;align-items:center;padding-left:70px;font-size:11.5px}
.main-nav a{padding:0 14px;border-right:1px dotted #bdbdbd;line-height:14px}
.main-nav a:first-child{padding-left:12px}
.main-nav a:last-child{border-right:none}

.hero{position:relative;height:308px;background:linear-gradient(100deg,#8a5a2e 0%,#c48a4e 35%,#d9a56b 60%,#a86d3a 100%)}
.hero-caption{position:absolute;left:64px;top:163px;width:331px;height:123px;background:rgba(190,180,170,.72);padding:14px 13px}
.hero-title{font-family:"Oswald",sans-serif;font-size:23px;color:#444;letter-spacing:.5px}
.hero-sub{font-size:16px;color:#333;margin-top:3px}
.hero-text{font-size:11px;color:#333;line-height:18px;margin-top:7px}
.hero-dots{position:absolute;left:740px;top:293px;display:flex;gap:4px}
.hero-dots i{width:9px;height:9px;border-radius:50%;background:#fff;display:block}
.hero-dots i:first-child{background:#777}

.section-title{position:absolute;top:492px;font-size:15px;font-weight:600;color:var(--red-text)}

.categories{position:absolute;left:63px;top:528px;width:197px;list-style:none;box-shadow:1px 1px 3px rgba(0,0,0,.12)}
.categories li{height:34.4px;border-bottom:1px solid var(--line);display:flex;align-items:center;justify-content:space-between;padding:0 12px;font-size:13px;background:#fbfbfb}
.categories li.active{background:var(--red);color:var(--white)}
.arrow{width:17px;height:17px;border-radius:50%;border:1px solid #ddd;display:flex;align-items:center;justify-content:center;background:#fff}
.active .arrow{background:#333;border-color:#333}

.product{position:absolute;width:159px;height:208px;border:1px solid var(--line);text-align:center}
.product-photo{width:110px;height:90px;margin:12px auto 0;border-radius:4px}
.product-name{font-size:12.5px;color:var(--red-text);margin-top:14px}
.product-desc{font-size:10.5px;color:var(--muted);text-align:left;padding:0 11px;line-height:18px;margin-top:5px}
.product-buy{display:flex;align-items:center;gap:14px;padding:0 11px;margin-top:6px;font-size:11px}
.add-cart{background:#eee;color:#666;font-size:9.5px;padding:4px 10px}

.site-footer{position:absolute;left:0;top:995px;width:860px;height:150px;background:var(--footer)}
.footer-col{position:absolute;top:14px;font-size:9.5px;color:#444}
.footer-col h4{font-size:11.5px;font-weight:400;color:#333;margin-bottom:7px}
.footer-col li{list-style:none;line-height:20.6px}
.newsletter{width:145px;height:24px;background:#c4c4c4;margin-top:18px;color:#fff;text-align:right;padding:2px 6px;font-size:15px}
.social{display:flex;gap:3px;margin-top:20px}
.social i{width:21px;height:21px;border-radius:50%;background:#8a8a8a;display:block}
.bottom-bar{position:absolute;left:0;top:1145px;width:860px;height:55px;background:var(--dark);color:#ddd;font-size:9px;padding:23px 64px}
</style>
</head>
<body>

<div class="top-bar">
  <nav class="top-links"><a>MY ACCOUNT</a><span class="sep">|</span><a>SIGN IN</a><span class="sep">|</span><a>CHECK OUT</a><span class="sep">|</span><a>CONTACT US</a></nav>
  <div class="cart">
    <svg width="14" height="12" viewBox="0 0 14 12"><path d="M0 1h2.5l2 7h7l2-5H4" fill="none" stroke="#ccc" stroke-width="1.2"/><circle cx="5.5" cy="10.5" r="1.1" fill="#ccc"/><circle cx="10.5" cy="10.5" r="1.1" fill="#ccc"/></svg>
    Cart (0) items
  </div>
</div>

<header class="site-header">
  <div class="brand">
    <div class="brand-name">Brindlewares</div>
    <div class="brand-tag">17th Generation Hayashida Bladesmith</div>
  </div>
  <div class="search">Search..
    <svg width="11" height="11" viewBox="0 0 11 11"><circle cx="4.5" cy="4.5" r="3.5" fill="none" stroke="#999" stroke-width="1.4"/><path d="M7 7l3 3" stroke="#999" stroke-width="1.6"/></svg>
  </div>
</header>

<nav class="main-nav">
  <a>HOME</a><a>ABOUT US</a><a>SHARPENING VIDEOS</a><a>KNIVES</a><a>TOOLS</a><a>INSTRUCTION</a><a>FAQ</a><a>NEWS</a><a>CONTACT US</a>
</nav>

<section class="hero" role="img" aria-label="Close-up photo of two knife blades on a wooden surface">
  <div class="hero-caption">
    <div class="hero-title">OUTDOOR KNIVES</div>
    <div class="hero-sub">DIGNISSIM PHARETRA ERO</div>
    <p class="hero-text">Jerta baditaut onsequser untur magni dolores eoquie volup tate msequi nesciunt. Voluptatem accusantium dolorem.</p>
  </div>
  <div class="hero-dots"><i></i><i></i><i></i><i></i></div>
</section>

<h2 class="section-title" style="left:62px">CATEGORIES</h2>
<h2 class="section-title" style="left:305px">PRODUCTS</h2>

<ul class="categories">
  <li class="active">Kitchen Knives<span class="arrow"><svg width="6" height="5"><path d="M0 2.5h5M3 .5l2 2-2 2" stroke="#fff" fill="none" stroke-width=".8"/></svg></span></li>
  <li>Neck Knives<span class="arrow"><svg width="6" height="5"><path d="M0 2.5h5M3 .5l2 2-2 2" stroke="#333" fill="none" stroke-width=".8"/></svg></span></li>
  <li>Outdoor Knives<span class="arrow"><svg width="6" height="5"><path d="M0 2.5h5M3 .5l2 2-2 2" stroke="#333" fill="none" stroke-width=".8"/></svg></span></li>
  <li>Bluefinch Knives<span class="arrow"><svg width="6" height="5"><path d="M0 2.5h5M3 .5l2 2-2 2" stroke="#333" fill="none" stroke-width=".8"/></svg></span></li>
  <li>Clearance Knives<span class="arrow"><svg width="6" height="5"><path d="M0 2.5h5M3 .5l2 2-2 2" stroke="#333" fill="none" stroke-width=".8"/></svg></span></li>
  <li>Premium Knives<span class="arrow"><svg width="6" height="5"><path d="M0 2.5h5M3 .5l2 2-2 2" stroke="#333" fill="none" stroke-width=".8"/></svg></span></li>
  <li>Misc. Product<span class="arrow"><svg width="6" height="5"><path d="M0 2.5h5M3 .5l2 2-2 2" stroke="#333" fill="none" stroke-width=".8"/></svg></span></li>
  <li>Waterstones<span class="arrow"><svg width="6" height="5"><path d="M0 2.5h5M3 .5l2 2-2 2" stroke="#333" fill="none" stroke-width=".8"/></svg></span></li>
  <li>DVDs<span class="arrow"><svg width="6" height="5"><path d="M0 2.5h5M3 .5l2 2-2 2" stroke="#333" fill="none" stroke-width=".8"/></svg></span></li>
  <li>T-Shirts<span class="arrow"><svg width="6" height="5"><path d="M0 2.5h5M3 .5l2 2-2 2" stroke="#333" fill="none" stroke-width=".8"/></svg></span></li>
  <li>Scissors<span class="arrow"><svg width="6" height="5"><path d="M0 2.5h5M3 .5l2 2-2 2" stroke="#333" fill="none" stroke-width=".8"/></svg></span></li>
  <li>Bladesmithing School<span class="arrow"><svg width="6" height="5"><path d="M0 2.5h5M3 .5l2 2-2 2" stroke="#333" fill="none" stroke-width=".8"/></svg></span></li>
</ul>

<article class="product" style="left:305px;top:529px">
  <div class="product-photo" role="img" aria-label="Chef knife with black handle" style="background:linear-gradient(135deg,#2a2a2a,#d8d8d8 60%,#f4f4f4)"></div>
  <div class="product-name">Neck Knives</div>
  <p class="product-desc">NasaFlo Unbreiakable Quantu mireax PtBait</p>
  <div class="product-buy">$146.00<span class="add-cart">ADD TO CART</span></div>
</article>
<article class="product" style="left:472px;top:529px">
  <div class="product-photo" role="img" aria-label="Knife with blue handle" style="background:linear-gradient(135deg,#e6e6e6,#cfcfcf 60%,#4a78b8)"></div>
  <div class="product-name">Outdoor Knives</div>
  <p class="product-desc">NasaFlo Unbreiakable Quantu mireax PtBait</p>
  <div class="product-buy">$146.00<span class="add-cart">ADD TO CART</span></div>
</article>
<article class="product" style="left:638px;top:529px">
  <div class="product-photo" role="img" aria-label="Set of three patterned knives" style="background:linear-gradient(135deg,#c7781f,#7a4a14 50%,#222)"></div>
  <div class="product-name">Clearance Knives</div>
  <p class="product-desc">NasaFlo Unbreiakable Quantu mireax PtBait</p>
  <div class="product-buy">$146.00<span class="add-cart">ADD TO CART</span></div>
</article>
<article class="product" style="left:305px;top:758px">
  <div class="product-photo" role="img" aria-label="Set of three black knives" style="background:linear-gradient(135deg,#f2f2f2,#2b2b2b 50%,#f2f2f2)"></div>
  <div class="product-name">Neck Knives</div>
  <p class="product-desc">NasaFlo Unbreiakable Quantu mireax PtBait</p>
  <div class="product-buy">$146.00<span class="add-cart">ADD TO CART</span></div>
</article>
<article class="product" style="left:472px;top:758px">
  <div class="product-photo" role="img" aria-label="Small knife with dark handle" style="background:linear-gradient(135deg,#e8e8e8,#cfcfcf 45%,#2e2a2a)"></div>
  <div class="product-name">Premium Knives</div>
  <p class="product-desc">NasaFlo Unbreiakable Quantu mireax PtBait</p>
  <div class="product-buy">$146.00<span class="add-cart">ADD TO CART</span></div>
</article>
<article class="product" style="left:638px;top:758px">
  <div class="product-photo" role="img" aria-label="Ceramic knife with pink handle" style="background:linear-gradient(135deg,#f4f4f4,#e2e2e2 50%,#d98cc9)"></div>
  <div class="product-name">Bluefinch Knives</div>
  <p class="product-desc">NasaFlo Unbreiakable Quantu mireax PtBait</p>
  <div class="product-buy">$146.00<span class="add-cart">ADD TO CART</span></div>
</article>

<footer class="site-footer">
  <div class="footer-col" style="left:65px"><h4>Customer Services</h4><ul><li>Shopping Guide</li><li>Contact Us</li><li>FAQ</li><li>Track My Order</li><li>Return Policy</li></ul></div>
  <div class="footer-col" style="left:223px"><h4>My Account</h4><ul><li>Sign in | Register</li><li>Order History</li><li>Messages</li><li>Points &amp; Coupons, Gifts</li><li>RMA Request</li></ul></div>
  <div class="footer-col" style="left:377px"><h4>Company Info</h4><ul><li>Legal window</li><li>About Us</li><li>Why Buy From Us</li><li>Security &amp; Privacy</li><li>Terms of Use</li></ul></div>
  <div class="footer-col" style="left:516px"><h4>Partner Program</h4><ul><li>Wholesale</li><li>Affiliate Program</li><li>Partner links</li><li>Drop-shipping</li></ul></div>
  <div class="footer-col" style="left:654px"><h4>Newsletter</h4>
    <div class="newsletter">»</div>
    <div class="social"><i></i><i></i><i></i><i></i></div>
  </div>
</footer>
<div class="bottom-bar">© 2013 Copyrights Reserved. All rights reserved.</div>

</body>
</html>
```